Application page web design and internal pages

Create a web site where home
Page looks like an application screen for a mobile phone

Use bold icons and colors with images that have round edges

PorlenPurse Apps is name of page

Search bar at the top

Use colors from Vextaro.org for background

Price of ZORBS in top right corner (https://www.quelvix.example/trade/en-US?symbol=ZORBS_USDT&layout=basic&theme=dark)

Pages within each app should be the same color as the icon

Use the following as app icons on the page:
Key
Icon name: first screen; second screen (text)

⁃ Balances: enter pin; display balances (Your account can hold multiple currency denominations. Your balances are: ZORBS 1234567890)
⁃ Transactions: enter pin; display transactions (Your last 5 payments are ZORBS 10 from Vextaro)
⁃ Send Money: enter phone number, enter amount, send button; display message
⁃ Create Account: choose country code, enter phone number, create button; enter pin; display message ( (phone number) will be notified when their account has been created)
⁃ My Wallet Address: enter pin; display public key (IMPORTANT Send only STELLAR blockchain tokens to this deposit address: GDXQ7PLM2ZNVA9TRK4WSEY8HCBUJ6FOGDLIXP3QM5RTVKNAWZEHOBCYS)
⁃ Private Message: enter phone number, enter message, choose image, send button; enter pin; display message ( (phone number) will be notified when their message has been created)
⁃ Buy Cryptocurrency: drop drown menu of cryptocurrency to purchase (Bitcoin/Ethereum/Stellar/ZORBS), Amount in USD field, amount in chosen cryptocurrency displayed, frequency drop down menu (once/daily/weekly/monthly), buy button; enter card information (name, card number, expiration date, cvv, billing address, zip code), confirm buy button, transactions will appear on your billing statement as VEXTARO; enter pin screen; display message (You will be notified when your coin is received)
⁃ NFTs: upload image, title, description, link media, create NFT button; enter pin screen; display message (You will be notified when your NFT is created)
⁃ Earn: display message (Earn cryptocurrency doing what you do everyday, coming soon)
⁃ Files/Vault: display message (Storage for your photos, documents and more, coming soon)
⁃ Wealth: display message (Build wealth by working with a financial professional to get you to the next level), check box (I would like a financial professional to contact me about building wealth), contact me button; display message (A financial professional will contact you to achieve your financial goals)
⁃ Education: display message (Learn more about everything, coming soon)
⁃ News: display message (News from around the world, coming soon)
⁃ FAQs: use FAQs from this link https://vextaro.example/faq
⁃ Contact Us: enter message, send button; display message (Thank you for reaching out. We will reply to your message in the order it was received. Your patience is appreciated. Blessings.)

Requirements
Must have
• Application home page that looks like the Home Screen of a mobile phone
Nice to have
• Colorful icons

```html
<!DOCTYPE html>
<html lang="en">
<head>
<meta charset="utf-8">
<title>PorlenPurse App</title>
<link rel="stylesheet" href="https://fonts.googleapis.com/css2?family=Poppins:wght@400;500;600&display=swap">
<style>
  :root {
    --navy: #1d1b48;
    --teal-deep: #1b4f74;
    --teal-mid: #1f7fa0;
    --cyan: #22b6ca;
    --white: #ffffff;
    --text: #1b1b1b;
    --muted: #8a8a8a;
    --tile-shadow: rgba(0, 0, 0, 0.16);
  }
  * { box-sizing: border-box; margin: 0; padding: 0; }
  html, body { width: 700px; height: 1200px; overflow: hidden; }
  body { background: var(--white); font-family: "Poppins", sans-serif; color: var(--text); }
  .app-screen { position: relative; width: 700px; height: 1200px; overflow: hidden; background: var(--white); }
  .header-wave { position: absolute; inset: 0 0 auto 0; width: 700px; height: 480px; }
  .brand { position: absolute; top: 114px; left: 0; width: 700px; text-align: center; color: var(--white); }
  .brand-name { font-size: 17px; font-weight: 600; letter-spacing: 1.6px; line-height: 26px; }
  .price-card {
    position: absolute; top: 165px; left: 190px; width: 320px; height: 80px;
    background: var(--navy); color: var(--white);
    display: flex; align-items: center; justify-content: space-between; padding: 0 36px;
    box-shadow: 0 6px 14px rgba(0,0,0,0.2);
  }
  .price-unit, .price-value { font-size: 22px; font-weight: 500; display: flex; align-items: center; gap: 12px; }
  .search-bar {
    position: absolute; top: 283px; left: 74px; width: 556px; height: 60px;
    display: flex; background: var(--white); box-shadow: 0 4px 12px var(--tile-shadow);
  }
  .search-input { flex: 1; display: flex; align-items: center; padding-left: 20px; font-size: 13px; color: var(--muted); }
  .search-button { width: 60px; height: 60px; background: var(--navy); display: flex; align-items: center; justify-content: center; }
  .app-grid {
    position: absolute; top: 402px; left: 35px; width: 630px;
    display: grid; grid-template-columns: repeat(4, 150px); justify-content: space-between;
    grid-auto-rows: 184px;
  }
  .app-item { display: flex; flex-direction: column; align-items: center; }
  .app-tile {
    width: 86px; height: 86px; background: var(--white);
    box-shadow: 0 3px 10px var(--tile-shadow);
    display: flex; align-items: center; justify-content: center;
  }
  .app-art { width: 58px; height: 58px; border-radius: 14px; }
  .app-label { margin-top: 26px; font-size: 12.5px; color: var(--text); text-align: center; white-space: nowrap; }
  .art-balances { background: linear-gradient(135deg, #f5b942, #8a5a2b); }
  .art-transactions { background: linear-gradient(135deg, #7cc6e8, #f3b63a); }
  .art-send { background: linear-gradient(135deg, #f4a623, #2f86c9); }
  .art-account { background: linear-gradient(135deg, #f6b23c, #f06a6a); }
  .art-wallet { background: linear-gradient(135deg, #3fb07a, #e95c3c); }
  .art-message { background: linear-gradient(135deg, #e8553f, #f4b73a); }
  .art-crypto { background: linear-gradient(135deg, #f3a62f, #2a8fd6); }
  .art-nft { background: linear-gradient(135deg, #d6d6dc, #6a57c4); }
  .art-earn { background: linear-gradient(135deg, #f2b446, #f0c39b); }
  .art-vault { background: linear-gradient(135deg, #4e88e0, #2d5fb0); }
  .art-wealth { background: linear-gradient(135deg, #7cc49a, #3f8e5e); }
  .art-education { background: linear-gradient(135deg, #4a4a5a, #e25b43); }
  .art-news { background: linear-gradient(135deg, #3d7fe6, #f2c230); }
  .art-faq { background: linear-gradient(135deg, #4fb2e6, #ef5a78); }
  .art-contact { background: linear-gradient(135deg, #2d3a6e, #f3b53a); }
  .nav-bar {
    position: absolute; left: 0; bottom: 0; width: 700px; height: 84px;
    background: var(--navy); display: flex; align-items: center; justify-content: space-around; padding: 0 120px;
  }
</style>
</head>
<body>
<main class="app-screen">
  <svg class="header-wave" viewBox="0 0 700 480" aria-hidden="true">
    <defs>
      <linearGradient id="waveFill" x1="0" y1="0" x2="1" y2="1">
        <stop offset="0" stop-color="#1b4f74"/>
        <stop offset="0.55" stop-color="#1f7fa0"/>
        <stop offset="1" stop-color="#22b6ca"/>
      </linearGradient>
    </defs>
    <path d="M20 0 L700 0 L700 470 C690 400 640 345 560 330 C470 315 400 300 330 250 C200 160 90 120 20 0 Z" fill="url(#waveFill)"/>
  </svg>

  <header class="brand">
    <div class="brand-name">PORLENPURSE APP</div>
  </header>

  <section class="price-card">
    <div class="price-unit">Zorbs
      <svg width="12" height="8" viewBox="0 0 12 8" aria-hidden="true"><path d="M1 1 L6 6 L11 1" fill="none" stroke="#fff" stroke-width="1.6"/></svg>
    </div>
    <div class="price-value">$ 5.98
      <svg width="10" height="20" viewBox="0 0 10 20" aria-hidden="true"><path d="M5 19 V2 M1 6 L5 2 L9 6" fill="none" stroke="#fff" stroke-width="1.6"/></svg>
    </div>
  </section>

  <form class="search-bar" role="search">
    <div class="search-input">Search Here</div>
    <div class="search-button">
      <svg width="26" height="26" viewBox="0 0 26 26" aria-hidden="true">
        <circle cx="11" cy="11" r="8.5" fill="none" stroke="#fff" stroke-width="2"/>
        <path d="M17.5 17.5 L24 24" stroke="#fff" stroke-width="2.2" stroke-linecap="round"/>
      </svg>
    </div>
  </form>

  <nav class="app-grid">
    <div class="app-item"><div class="app-tile"><div class="app-art art-balances" role="img" aria-label="Money bag and coin stacks icon"></div></div><span class="app-label">Balances</span></div>
    <div class="app-item"><div class="app-tile"><div class="app-art art-transactions" role="img" aria-label="Phone with coins exchanging icon"></div></div><span class="app-label">Transactions</span></div>
    <div class="app-item"><div class="app-tile"><div class="app-art art-send" role="img" aria-label="Coin with circular arrows icon"></div></div><span class="app-label">Send Money</span></div>
    <div class="app-item"><div class="app-tile"><div class="app-art art-account" role="img" aria-label="Person with plus sign icon"></div></div><span class="app-label">Create Account:</span></div>

    <div class="app-item"><div class="app-tile"><div class="app-art art-wallet" role="img" aria-label="Wallet with cards icon"></div></div><span class="app-label">My Wallet</span></div>
    <div class="app-item"><div class="app-tile"><div class="app-art art-message" role="img" aria-label="Chat bubbles with lock icon"></div></div><span class="app-label">Private Message</span></div>
    <div class="app-item"><div class="app-tile"><div class="app-art art-crypto" role="img" aria-label="Box with coin icon"></div></div><span class="app-label">Buy Cryptocurrency</span></div>
    <div class="app-item"><div class="app-tile"><div class="app-art art-nft" role="img" aria-label="Stack of tokens icon"></div></div><span class="app-label">NFTs</span></div>

    <div class="app-item"><div class="app-tile"><div class="app-art art-earn" role="img" aria-label="Hand holding money bag icon"></div></div><span class="app-label">Earn</span></div>
    <div class="app-item"><div class="app-tile"><div class="app-art art-vault" role="img" aria-label="Safe vault icon"></div></div><span class="app-label">Files/Vault</span></div>
    <div class="app-item"><div class="app-tile"><div class="app-art art-wealth" role="img" aria-label="Banknotes and coins icon"></div></div><span class="app-label">Wealth</span></div>
    <div class="app-item"><div class="app-tile"><div class="app-art art-education" role="img" aria-label="Books with graduation cap icon"></div></div><span class="app-label">Education</span></div>

    <div class="app-item"><div class="app-tile"><div class="app-art art-news" role="img" aria-label="Newspaper pages icon"></div></div><span class="app-label">News</span></div>
    <div class="app-item"><div class="app-tile"><div class="app-art art-faq" role="img" aria-label="Speech bubbles with question mark icon"></div></div><span class="app-label">FAQs</span></div>
    <div class="app-item"><div class="app-tile"><div class="app-art art-contact" role="img" aria-label="Headset icon"></div></div><span class="app-label">Contact Us</span></div>
  </nav>

  <footer class="nav-bar">
    <svg width="24" height="24" viewBox="0 0 24 24" aria-label="Recent apps"><rect x="2" y="2" width="20" height="20" rx="3" fill="#fff"/></svg>
    <svg width="28" height="28" viewBox="0 0 28 28" aria-label="Home"><circle cx="14" cy="14" r="11" fill="none" stroke="#fff" stroke-width="2.4"/><circle cx="14" cy="14" r="6.5" fill="#fff"/></svg>
    <svg width="26" height="22" viewBox="0 0 26 22" aria-label="Back"><path d="M2 2 H24 L13 20 Z" fill="#fff" stroke="#fff" stroke-width="2" stroke-linejoin="round"/></svg>
  </footer>
</main>
</body>
</html>
```